Lawn Sign For Construction Projects - Brisk Harbor

This contest is for a lawn sign that will be placed in the front yard of recently completed construction projects. The goal here is to have a bold advertising sign that is visible from a vehicle driving past.

We are still deciding on the default size for our sign, we also may use multiple sizes. The two sizes we will more than likely be using are: 18"h x 24"w and 24"h x 36"w.

Preference will be given to designers that submit original designs that tie into our current brand and are either in both the size formats listed above or are easy to scale in photoshop or illustrator.

In the files, you will see our logo and an example of a lawn sign.

Please contact us with any questions or comments you may have!

Thank You,
- The Brisk Harbor Team
Updates

Project Deadline Extended Reason: We Currently to not have any designs worth choosing. Added Monday, March 21, 2016

Industry/Entity Type

Residential Construction

Colors
34a7d8
ffffff
faa54b

Requirements
Nice to have
• 1. The sign must tie into our current branding and color scheme.
• 2. The sign must be clearly visible and readable.
• 3. The sign must include our phone number in readable print.
• 4. Our website written in small print along the bottom of the sign.
• 5. Must mention we install the following products:
• a.) Solar
• b.) Roofing
• c.) Windows
• d.) Artificial Lawn
• e.) Whole House Fans
• f.) Patio Covers

```html
<!DOCTYPE html>
<html lang="en">
<head>
<meta charset="utf-8">
<title>Brisk Harbor – Lawn Sign</title>
<link rel="stylesheet" href="https://fonts.googleapis.com/css2?family=Cinzel:wght@700&family=Montserrat:wght@700&family=Open+Sans:wght@600;700&display=swap">
<style>
  :root {
    --lime: #a6cc3b;
    --lime-light: #b5d64a;
    --lime-dark: #93bd2f;
    --green-deep: #3f5e0f;
    --orange: #f47a2a;
    --orange-deep: #ea6c20;
    --white: #ffffff;
    --brand-blue: #2a93cf;
    --ink: #2b2b2b;
    --sign-frame: #f7a531;
    --sign-face: #fbf0c4;
    --sign-text: #5a3a16;
  }
  html, body {
    margin: 0;
    padding: 0;
    width: 1200px;
    height: 900px;
    overflow: hidden;
    background: var(--white);
  }
  .lawn-sign {
    position: relative;
    width: 1200px;
    height: 900px;
    overflow: hidden;
    background: var(--lime);
  }
  .backdrop {
    position: absolute;
    inset: 0;
  }
  .brand {
    position: absolute;
    top: 92px;
    left: 860px;
    width: 320px;
    text-align: center;
  }
  .brand-dot {
    display: block;
    width: 80px;
    height: 80px;
    margin: 0 auto 12px;
    border-radius: 50%;
    background: var(--orange);
  }
  .brand-name {
    margin: 0;
    font-family: "Montserrat", sans-serif;
    font-weight: 700;
    font-size: 38px;
    letter-spacing: 0.5px;
    color: var(--brand-blue);
    line-height: 1.1;
  }
  .brand-phone {
    margin: 4px 0 0;
    font-family: "Open Sans", sans-serif;
    font-weight: 700;
    font-size: 27px;
    color: var(--ink);
  }
  .services {
    position: absolute;
    top: 358px;
    left: 140px;
    display: grid;
    grid-template-columns: 360px 460px;
    row-gap: 52px;
    margin: 0;
    padding: 0;
    list-style: none;
  }
  .service {
    display: flex;
    align-items: center;
    gap: 32px;
    font-family: "Cinzel", serif;
    font-weight: 700;
    font-size: 32px;
    letter-spacing: 1.5px;
    color: var(--white);
    line-height: 1;
    text-shadow: 0 2px 3px rgba(47, 72, 8, 0.75), 0 0 10px rgba(47, 72, 8, 0.45);
  }
  .service-arrow {
    width: 44px;
    height: 14px;
    flex: none;
    filter: drop-shadow(0 1px 2px rgba(47, 72, 8, 0.7));
  }
  .web-sign {
    position: absolute;
    left: 762px;
    top: 646px;
    width: 410px;
    height: 180px;
  }
  .web-address {
    position: absolute;
    left: 830px;
    top: 719px;
    width: 270px;
    margin: 0;
    text-align: center;
    font-family: "Open Sans", sans-serif;
    font-weight: 700;
    font-size: 23px;
    color: var(--sign-text);
  }
</style>
</head>
<body>
<main class="lawn-sign">
  <svg class="backdrop" width="1200" height="900" viewBox="0 0 1200 900" aria-hidden="true">
    <polygon points="0,0 380,0 0,210" fill="var(--orange)"/>
    <polygon points="0,210 380,0 560,0 0,420" fill="var(--lime-dark)"/>
    <polygon points="560,0 1200,0 1200,900 980,900 420,420" fill="var(--lime-light)"/>
    <polygon points="0,690 560,900 0,900" fill="var(--lime-dark)"/>
    <polygon points="520,900 760,560 1000,900" fill="var(--lime-dark)" opacity="0.55"/>
    <polygon points="560,0 950,0 770,170" fill="var(--orange-deep)"/>
    <polygon points="950,0 1200,0 1200,360 770,170" fill="var(--white)"/>
  </svg>
  <svg class="backdrop" width="1200" height="900" viewBox="0 0 1200 900" role="img" aria-label="Faint butterfly decorations scattered over the green background">
    <defs>
      <radialGradient id="faint-glow">
        <stop offset="0" stop-color="#7fb62a" stop-opacity="0.45"/>
        <stop offset="1" stop-color="#7fb62a" stop-opacity="0"/>
      </radialGradient>
    </defs>
    <ellipse cx="530" cy="200" rx="80" ry="70" fill="url(#faint-glow)"/>
    <ellipse cx="1010" cy="450" rx="75" ry="70" fill="url(#faint-glow)"/>
    <ellipse cx="620" cy="790" rx="110" ry="100" fill="url(#faint-glow)"/>
  </svg>

  <header class="brand">
    <span class="brand-dot" aria-hidden="true"></span>
    <h1 class="brand-name">BRISK HARBOR</h1>
    <p class="brand-phone">0800-555-0192</p>
  </header>

  <ul class="services">
    <li class="service"><svg class="service-arrow" viewBox="0 0 44 14" aria-hidden="true"><path d="M0 7H42M35 1l7 6-7 6" fill="none" stroke="var(--white)" stroke-width="2.5"/></svg>Solar</li>
    <li class="service"><svg class="service-arrow" viewBox="0 0 44 14" aria-hidden="true"><path d="M0 7H42M35 1l7 6-7 6" fill="none" stroke="var(--white)" stroke-width="2.5"/></svg>Artificial Lawn</li>
    <li class="service"><svg class="service-arrow" viewBox="0 0 44 14" aria-hidden="true"><path d="M0 7H42M35 1l7 6-7 6" fill="none" stroke="var(--white)" stroke-width="2.5"/></svg>Roofing</li>
    <li class="service"><svg class="service-arrow" viewBox="0 0 44 14" aria-hidden="true"><path d="M0 7H42M35 1l7 6-7 6" fill="none" stroke="var(--white)" stroke-width="2.5"/></svg>Whole House Fans</li>
    <li class="service"><svg class="service-arrow" viewBox="0 0 44 14" aria-hidden="true"><path d="M0 7H42M35 1l7 6-7 6" fill="none" stroke="var(--white)" stroke-width="2.5"/></svg>Windows</li>
    <li class="service"><svg class="service-arrow" viewBox="0 0 44 14" aria-hidden="true"><path d="M0 7H42M35 1l7 6-7 6" fill="none" stroke="var(--white)" stroke-width="2.5"/></svg>Patio Covers</li>
  </ul>

  <svg class="web-sign" viewBox="0 0 410 180" aria-hidden="true">
    <polygon points="6,30 300,30 300,4 404,90 300,176 300,150 6,150 30,90" fill="var(--sign-frame)"/>
    <polygon points="34,48 316,48 316,40 376,90 316,140 316,132 34,132 52,90" fill="var(--sign-face)"/>
  </svg>
  <p class="web-address">www.briskharbor.com</p>
</main>
</body>
</html>
```